Clara Runberg - Powerpoint slides

I am an educator and lecturer - I use powerpoint slides for my presentations. I would like to use my current logo and branding to create personalised powerpoint presentations.

I need a file with so I can select my personalized Powerpoint slides: I would like 3 colour variations of the following slides (design and layout is the same for all colours, with just the colour shades change)
1. Title Slide
2. Title & Content
3. Section Header
4. 2 content slide
5. Blank Slide

Note on colours: 3+ variations would be great - suggest background colours to be Turqoise
Dark/Grey Charcoal \
White
PLUS one free choice colour scheme from the designers.

Target Market(s)

Physiotherapists
Yoga Teachers
Students (yoga students and physiotherapy students)
Medical Professionals

Industry/Entity Type

Health And Wellness

Font styles to use
Serif
Sans Serif

Colors
33b8a4
876aae
0255a3

Requirements
Must have
• See the slide types in the brief description.
• Each slide should stay pretty much in the same colour, just different intensity of the shade.
• Please use the designs from my uploaded files.
• 3+ different colour variations for the regular content for slides
Nice to have
• Background patterns over part of the screen.
Should not have
• Not too many colour variations - I have chosen the ones I like as examples.

```html
<!DOCTYPE html>
<html lang="en">
<head>
<meta charset="utf-8">
<title>Clara Runberg – Slide Templates</title>
<link href="https://fonts.googleapis.com/css2?family=Poiret+One&family=Lato:wght@300;400&display=swap" rel="stylesheet">
<style>
  :root {
    --teal: #2f9c8e;
    --teal-deep: #1f8479;
    --teal-dark: #17786f;
    --purple: #9c83c2;
    --purple-deep: #7c62a8;
    --rose: #a57cae;
    --blue: #2f6fb3;
    --blue-deep: #1c519a;
    --ink: #6f6f6f;
    --text-light: #9a9a9a;
    --white: #ffffff;
    --heading-teal: #38a698;
  }
  * { box-sizing: border-box; margin: 0; padding: 0; }
  html, body { width: 800px; height: 1200px; overflow: hidden; background: var(--white); }
  body { position: relative; font-family: "Lato", Arial, sans-serif; }

  .slide {
    position: absolute; width: 392px; height: 220px; overflow: hidden;
    box-shadow: 0 2px 5px rgba(0,0,0,0.28);
  }
  .photo { position: absolute; inset: 0; }
  .ornament {
    position: absolute; width: 230px; height: 230px; border-radius: 50%;
    background: radial-gradient(circle, rgba(255,255,255,0) 30%, rgba(255,255,255,0.16) 52%, rgba(255,255,255,0.05) 70%, rgba(255,255,255,0) 72%);
  }
  .ornament.right { right: -40px; top: -5px; }
  .ornament.left { left: -120px; top: -5px; }

  .brand {
    position: absolute; top: 34px; display: flex; align-items: center; gap: 4px;
    font-family: "Poiret One", sans-serif; font-size: 11px; color: var(--white);
  }
  .brand .dot { width: 10px; height: 10px; border: 1px solid currentColor; border-radius: 50%; }
  .brand.left { left: 16px; }
  .brand.right { right: 16px; }

  .title-block { position: absolute; color: var(--white); }
  .title-block.left { left: 15px; top: 148px; }
  .title-block.right { right: 15px; top: 152px; text-align: right; }
  .title-block h1 { font-family: "Poiret One", sans-serif; font-weight: 400; font-size: 22px; line-height: 1; white-space: nowrap; }
  .title-block p { font-family: "Poiret One", sans-serif; font-size: 6px; margin-top: 8px; }

  .photo.pose-teal { background: linear-gradient(180deg, #3e9a91 0%, #33968a 50%, #24876f 100%); }
  .photo.pose-purple { background: linear-gradient(180deg, #9d86c4 0%, #9278b8 55%, #8665ab 100%); }
  .photo.pose-blue { background: linear-gradient(180deg, #3877b6 0%, #2f6db0 55%, #245da4 100%); }
  .photo.sea-teal { background: linear-gradient(180deg, #2c8d86 0%, #2f9a8d 45%, #27917e 100%); }
  .photo.sea-rose { background: linear-gradient(180deg, #8e6aa7 0%, #a47cae 45%, #8660a6 100%); }
  .photo.sea-blue { background: linear-gradient(180deg, #1f5fa2 0%, #2a6cb1 45%, #1f539d 100%); }

  /* white content slides */
  .content { background: var(--white); }
  .content .brand { color: var(--heading-teal); top: 14px; right: 16px; }
  .slide-title {
    position: absolute; left: 12px; top: 12px;
    font-family: "Poiret One", sans-serif; font-size: 17px; color: var(--ink); font-weight: 400;
  }
  .slide-title::after {
    content: ""; position: absolute; left: 0; top: 26px; width: 16px; height: 1.5px; background: var(--teal);
  }
  .footer {
    position: absolute; left: 0; right: 0; bottom: 0; height: 12px; background: var(--teal-deep);
    font-size: 4.5px; color: var(--white); padding-left: 16px; line-height: 12px;
  }
  .page-no {
    position: absolute; right: 28px; bottom: 2px; width: 14px; height: 10px; background: var(--white);
    font-size: 5px; color: var(--ink); text-align: center; line-height: 10px;
  }
  .faint-ornament {
    position: absolute; right: -20px; top: 80px; width: 200px; height: 200px; border-radius: 50%;
    background: radial-gradient(circle, rgba(51,184,164,0) 30%, rgba(51,184,164,0.08) 52%, rgba(51,184,164,0) 70%);
  }

  .band {
    position: absolute; left: 0; right: 0; top: 53px; height: 89px;
    background: linear-gradient(180deg, #2f9387 0%, #2a8d82 60%, #217f73 100%);
  }
  .key-icon {
    position: absolute; top: 66px; width: 62px; height: 62px; border-radius: 50%;
    border: 2px solid rgba(255,255,255,0.7);
  }
  .key-icon.one { left: 31px; background: radial-gradient(circle, #c8d8de, #8ca5a8); }
  .key-icon.two { left: 163px; background: linear-gradient(180deg, #f2b45e, #1f3d66); }
  .key-icon.three { left: 297px; background: radial-gradient(circle, #c3786f, #7a4f44); }
  .key-col { position: absolute; top: 146px; width: 112px; text-align: center; }
  .key-col h3 { font-family: "Lato", sans-serif; font-weight: 400; font-size: 6px; color: var(--heading-teal); }
  .key-col p { font-size: 3.8px; line-height: 1.55; color: var(--text-light); margin-top: 3px; }
  .key-col.one { left: 6px; }
  .key-col.two { left: 138px; }
  .key-col.three { left: 272px; }

  .image-left {
    position: absolute; left: 12px; top: 53px; width: 177px; height: 132px;
    background: linear-gradient(180deg, #42464f 0%, #d88a3a 48%, #f4c46b 56%, #3b3a3a 70%, #2a2b2d 100%);
  }
  .points { position: absolute; left: 211px; width: 150px; font-size: 3.8px; line-height: 1.6; color: var(--text-light); }
  .points .lead { color: var(--heading-teal); }
  .points ul { list-style: disc; padding-left: 8px; }
  .points.p1 { top: 57px; }
  .points.p2 { top: 102px; }
  .points.p3 { top: 148px; }
</style>
</head>
<body>

  <!-- Title slides: teal, purple, blue (pose) -->
  <section class="slide title-slide" style="left:4px; top:10px;">
    <div class="photo pose-teal" role="img" aria-label="Yoga pose on a rocky shore, teal tint"></div>
    <div class="ornament right" role="img" aria-label="Large faint mandala pattern"></div>
    <div class="brand left"><span class="dot"></span>Clara Runberg</div>
    <div class="title-block left"><h1>Your Title Goes Here</h1><p>Your Subtitle Goes Here</p></div>
  </section>

  <section class="slide title-slide" style="left:404px; top:10px;">
    <div class="photo pose-purple" role="img" aria-label="Yoga pose on a rocky shore, purple tint"></div>
    <div class="ornament right" role="img" aria-label="Large faint mandala pattern"></div>
    <div class="brand left"><span class="dot"></span>Clara Runberg</div>
    <div class="title-block left"><h1>Your Title Goes Here</h1><p>Your Subtitle Goes Here</p></div>
  </section>

  <section class="slide title-slide" style="left:4px; top:250px;">
    <div class="photo pose-blue" role="img" aria-label="Yoga pose on a rocky shore, blue tint"></div>
    <div class="ornament right" role="img" aria-label="Large faint mandala pattern"></div>
    <div class="brand left"><span class="dot"></span>Clara Runberg</div>
    <div class="title-block left"><h1>Your Title Goes Here</h1><p>Your Subtitle Goes Here</p></div>
  </section>

  <!-- Title slides: sea variants -->
  <section class="slide title-slide" style="left:404px; top:250px;">
    <div class="photo sea-teal" role="img" aria-label="Yoga pose by the sea at dusk, teal tint"></div>
    <div class="ornament left" role="img" aria-label="Large faint mandala pattern"></div>
    <div class="brand right"><span class="dot"></span>Clara Runberg</div>
    <div class="title-block right"><h1>Your Title Goes Here</h1><p>Your Subtitle Goes Here</p></div>
  </section>

  <section class="slide title-slide" style="left:4px; top:490px;">
    <div class="photo sea-rose" role="img" aria-label="Yoga pose by the sea at dusk, rose purple tint"></div>
    <div class="ornament left" role="img" aria-label="Large faint mandala pattern"></div>
    <div class="brand right"><span class="dot"></span>Clara Runberg</div>
    <div class="title-block right"><h1>Your Title Goes Here</h1><p>Your Subtitle Goes Here</p></div>
  </section>

  <section class="slide title-slide" style="left:404px; top:490px;">
    <div class="photo sea-blue" role="img" aria-label="Yoga pose by the sea at dusk, blue tint"></div>
    <div class="ornament left" role="img" aria-label="Large faint mandala pattern"></div>
    <div class="brand right"><span class="dot"></span>Clara Runberg</div>
    <div class="title-block right"><h1>Your Title Goes Here</h1><p>Your Subtitle Goes Here</p></div>
  </section>

  <!-- Blank slide -->
  <section class="slide content" style="left:4px; top:730px;">
    <h2 class="slide-title">Your Blank Slide</h2>
    <div class="brand right"><span class="dot"></span>Clara Runberg</div>
    <div class="faint-ornament" role="img" aria-label="Faint mandala pattern"></div>
    <div class="footer">Yoga Teachers Physiotherapists</div>
    <div class="page-no">7</div>
  </section>

  <!-- Three key point slide -->
  <section class="slide content" style="left:404px; top:730px;">
    <h2 class="slide-title">Three Key Point Page</h2>
    <div class="brand right"><span class="dot"></span>Clara Runberg</div>
    <div class="band" role="img" aria-label="Teal tinted photo of a yoga pose by the sea"></div>
    <div class="key-icon one" role="img" aria-label="Round photo with a line icon"></div>
    <div class="key-icon two" role="img" aria-label="Round sunset photo with a meditation icon"></div>
    <div class="key-icon three" role="img" aria-label="Round photo with a lotus icon"></div>
    <div class="key-col one"><h3>Heading Here</h3><p>Short supporting text sits here to explain the heading above in two or three calm lines for the audience.</p></div>
    <div class="key-col two"><h3>Heading Here</h3><p>Short supporting text sits here to explain the heading above in two or three calm lines for the audience.</p></div>
    <div class="key-col three"><h3>Heading Here</h3><p>Short supporting text sits here to explain the heading above in two or three calm lines for the audience.</p></div>
    <div class="footer">Yoga Teachers Physiotherapists</div>
    <div class="page-no">8</div>
  </section>

  <!-- Image left slide -->
  <section class="slide content" style="left:209px; top:970px;">
    <h2 class="slide-title">Image Left</h2>
    <div class="brand right"><span class="dot"></span>Clara Runberg</div>
    <div class="image-left" role="img" aria-label="Photo of a person meditating by a lake at sunset"></div>
    <div class="points p1"><p><span class="lead">Key point here,</span> with a short line of supporting text.</p>
      <ul><li>First detail for this point</li><li>Second detail for this point</li></ul></div>
    <div class="points p2"><p><span class="lead">Key point here,</span> with a short line of supporting text.</p>
      <ul><li>First detail for this point</li><li>Second detail for this point</li></ul></div>
    <div class="points p3"><p><span class="lead">Key point here,</span> with a short line of supporting text.</p>
      <ul><li>First detail for this point</li><li>Second detail for this point</li></ul></div>
    <div class="footer">Yoga Teachers Physiotherapists</div>
    <div class="page-no">9</div>
  </section>

</body>
</html>
```